Design a Website for an IT Support Company

We are an IT support company that provides commercial IT support and services to small and medium sized businesses. We are in need of a website to be developed for our business.
We would like to work with someone who is either familiar with the IT field, or has developed a website for an IT support company in the past.
Some examples of designs/layouts that we like:
https://www.veldaworks.example/
http://www.marsbyquill.example/
http://817kq.example/
http://www.olbenstructures.example/
http://www.bykq.example/
I have attached a word document that gives a menu system/page layout format that we would like for our website as well as branch office phone numbers. Our logo is also attached that you can use for your design purposes. We currently do not have copy produced for all of the pages outlined in the word document, but would get this done during the project with the selected designer.
We would like the website to be SEO friendly & fully responsive. We would prefer a Wordpress format, however, we are open to HTML formats as well.

```html
<!DOCTYPE html>
<html lang="en">
<head>
<meta charset="utf-8">
<title>Corvane IT – IT Support</title>
<link href="https://fonts.googleapis.com/css2?family=Open+Sans:wght@400;600;700&display=swap" rel="stylesheet">
<style>
:root{
  --blue:#0b6fc1;
  --blue-dark:#0a5fa6;
  --ink:#222;
  --muted:#555;
  --light-bg:#efefef;
  --grey-band:#7a7b7d;
  --grey-circle:#58595b;
  --white:#fff;
  --footer:#0b6fc2;
}
*{margin:0;padding:0;box-sizing:border-box}
html,body{width:1200px;height:2497px;overflow:hidden}
body{font-family:"Open Sans",Arial,sans-serif;color:var(--ink);background:var(--white);position:relative}
a{text-decoration:none}
.abs{position:absolute}
.btn{position:absolute;background:var(--blue);color:var(--white);font-weight:700;font-size:11px;letter-spacing:.5px;display:flex;align-items:center;justify-content:center;text-transform:uppercase;text-decoration:none}

/* header */
.hero{left:0;top:0;width:1200px;height:719px;background:linear-gradient(100deg,#e9edf1 0%,#dfe5ea 35%,#cdd6de 60%,#8a97a8 80%,#c9d2da 100%)}
.brand{position:absolute;display:flex;align-items:center;gap:12px;font-weight:600}
.brand .dot{width:34px;height:34px;border-radius:50%}
.header-brand{left:133px;top:40px;font-size:34px;color:#2a2f36}
.header-brand .dot{background:var(--blue)}
.nav{left:576px;top:20px;display:flex;font-size:10px;font-weight:700;text-transform:uppercase;line-height:1}
.nav a{color:#222;padding:5px 7px;margin-right:14px;white-space:nowrap}
.nav a:last-child{margin-right:0}
.nav a.active{background:var(--blue);color:var(--white)}
.call{left:916px;top:14px;display:flex;align-items:center;gap:8px}
.call small{display:block;font-size:9px;font-weight:700;color:#333}
.call strong{display:block;font-size:17px;color:var(--blue);font-weight:700;line-height:1.1}
.hero-title{left:318px;top:240px;font-size:50px;font-weight:600;color:var(--blue)}
.hero-text{left:322px;top:316px;width:360px;font-size:15px;line-height:1.5;color:#333}
.hero .btn{left:323px;top:388px;width:118px;height:36px;font-size:12px}
.dots{left:572px;top:648px;display:flex;gap:8px}
.dots i{width:11px;height:11px;border-radius:50%;background:#fff;display:block}
.dots i.on{background:#d13a2c}

/* services */
.services{left:0;top:719px;width:1200px;height:581px;background:var(--light-bg)}
.section-title{position:absolute;left:0;width:1200px;text-align:center;font-size:20px;font-weight:700;text-transform:uppercase}
.section-title::after{content:"";display:block;width:36px;height:2px;background:currentColor;margin:14px auto 0}
.services .section-title{top:58px;color:var(--blue)}
.service{position:absolute;top:159px;width:300px;margin-left:-150px;text-align:center}
.icon-wrap{position:relative;width:104px;height:104px;margin:0 auto}
.icon-wrap::before{content:"";position:absolute;left:52px;top:10px;width:120px;height:84px;background:linear-gradient(90deg,rgba(0,0,0,.07),rgba(0,0,0,0));transform:rotate(35deg);transform-origin:0 50%}
.icon-circle{position:absolute;inset:0;border-radius:50%;background:#fff;border:1px solid #ddd;display:flex;align-items:center;justify-content:center}
.service h3{margin-top:42px;font-size:15px;font-weight:700;text-transform:uppercase}
.service ul{list-style:none;margin-top:20px;font-size:11px;line-height:22.5px;color:#444}
.service .btn{position:relative;margin:30px auto 0;width:98px;height:28px;font-size:10px}

/* why */
.why{left:0;top:1300px;width:1200px;height:482px;background:var(--grey-band);color:var(--white)}
.why .section-title{top:52px;color:var(--white)}
.why .section-title::after{display:none}
.why-mark{left:136px;top:168px;width:40px;height:40px;border:3px solid #fff;border-radius:50%}
.why-text{left:133px;top:238px;width:297px;font-size:12px;line-height:19px;text-align:justify}
.why .btn{left:136px;top:362px;width:97px;height:28px;font-size:10px}
.feature{position:absolute;display:flex;gap:16px;width:280px}
.feature .fc{position:relative;flex:none;width:88px;height:88px;border-radius:50%;background:var(--grey-circle);display:flex;align-items:center;justify-content:center}
.feature .fc::before{content:"";position:absolute;left:44px;top:8px;width:90px;height:72px;background:linear-gradient(90deg,rgba(0,0,0,.12),rgba(0,0,0,0));transform:rotate(40deg);transform-origin:0 50%;z-index:-1}
.feature h4{font-size:12px;font-weight:700;text-transform:uppercase;margin-top:18px}
.feature p{font-size:11px;line-height:18px;margin-top:6px}

/* testimonials */
.testimonials{left:0;top:1782px;width:1200px;height:386px;background:var(--white)}
.testimonials .section-title{top:64px;color:var(--blue)}
.quote-mark{position:absolute;font-size:56px;color:#ccc;font-family:Georgia,serif;line-height:1}
.quote{left:366px;top:158px;width:496px;text-align:center;font-size:12px;line-height:20px;color:#444}
.arrow{position:absolute;top:178px;width:40px;height:40px;border-radius:50%;background:#c4c4c4;display:flex;align-items:center;justify-content:center}
.author{left:0;top:290px;width:1200px;text-align:center;font-size:12px;font-weight:600;color:var(--blue);text-transform:uppercase}
.author::before{content:"";display:block;width:140px;height:1px;background:#ccc;margin:0 auto 12px}

/* footer */
.footer{left:0;top:2168px;width:1200px;height:329px;background:var(--footer);color:var(--white)}
.footer-brand{left:133px;top:70px;font-size:34px;color:var(--white)}
.footer-brand .dot{background:var(--white)}
.footer-divider{left:388px;top:52px;width:1px;height:100px;background:rgba(255,255,255,.25)}
.branch{position:absolute;top:86px}
.branch span{display:block;font-size:11px}
.branch strong{display:block;font-size:17px;font-weight:700;margin-top:2px}
.footer-rule{left:133px;top:208px;width:935px;height:1px;background:rgba(255,255,255,.25)}
.footer-links{left:135px;top:248px;font-size:11px}
.footer-links a{color:var(--white)}
.footer-links b{font-weight:400;margin:0 7px;opacity:.7}
.copyright{left:852px;top:248px;font-size:11px}
</style>
</head>
<body>

<section class="abs hero">
  <div class="abs" role="img" aria-label="Photo of a smiling support agent wearing a headset, working at a laptop in a bright office" style="inset:0"></div>
  <div class="brand header-brand"><span class="dot"></span>Corvane IT</div>
  <nav class="abs nav"><a class="active" href="#">Home</a><a href="#">Services</a><a href="#">Why Corvane IT</a><a href="#">Contact</a></nav>
  <div class="abs call">
    <svg width="26" height="26" viewBox="0 0 26 26"><circle cx="13" cy="13" r="11.5" fill="none" stroke="#0b6fc1" stroke-width="2"/><path d="M9 7l3 3-1.5 1.5a8 8 0 0 0 4 4L16 14l3 3-2 2c-5 0-10-5-10-10z" fill="#0b6fc1"/></svg>
    <div><small>CALL US</small><strong>555-010-4400</strong></div>
  </div>
  <h1 class="abs hero-title">IT Support</h1>
  <p class="abs hero-text">Lorem Ipsum is simply dummy text of the printing and typesetting industry.</p>
  <a class="btn" href="#">Read More</a>
  <div class="abs dots"><i></i><i class="on"></i><i></i><i></i></div>
</section>

<section class="abs services">
  <h2 class="section-title">Our Services</h2>

  <div class="service" style="left:291px">
    <div class="icon-wrap"><div class="icon-circle">
      <svg width="40" height="48" viewBox="0 0 40 48" fill="none" stroke="#0b6fc1" stroke-width="3"><ellipse cx="20" cy="8" rx="16" ry="5"/><path d="M4 8v32c0 3 7 5 16 5s16-2 16-5V8M4 19c0 3 7 5 16 5s16-2 16-5M4 30c0 3 7 5 16 5s16-2 16-5"/></svg>
    </div></div>
    <h3>Data</h3>
    <ul><li>Managed IT Services</li><li>IT Support &amp; Consulting</li><li>IT Helpdesk Services</li><li>Network Security</li><li>Data Backup &amp; Recovery</li></ul>
    <a class="btn" href="#">Read More</a>
  </div>

  <div class="service" style="left:597px">
    <div class="icon-wrap"><div class="icon-circle">
      <svg width="60" height="40" viewBox="0 0 60 40" fill="none" stroke="#0b6fc1" stroke-width="3"><path d="M14 36a11 11 0 0 1-1-22 15 15 0 0 1 29-3 12 12 0 0 1 4 25z"/><path d="M22 26h16" stroke-linecap="round"/></svg>
    </div></div>
    <h3>Cloud</h3>
    <ul><li>Workline Office Migrations</li><li>Nimbra Cloud Management Services</li><li>Cloud Migration Services</li><li>Hosted Virtual Servers</li><li>Hosted Telephone Systems</li></ul>
    <a class="btn" href="#">Read More</a>
  </div>

  <div class="service" style="left:907px">
    <div class="icon-wrap"><div class="icon-circle">
      <svg width="40" height="56" viewBox="0 0 40 56" fill="#0b6fc1"><rect x="13" y="2" width="14" height="30" rx="7"/><path d="M6 24a14 14 0 0 0 28 0" fill="none" stroke="#0b6fc1" stroke-width="3"/><rect x="18.5" y="38" width="3" height="14"/></svg>
    </div></div>
    <h3>Voice</h3>
    <ul><li>Quillo PBX Consulting</li><li>Business Telephone Systems</li><li>Multiple Office Phone Systems</li><li>Tonewell Telephone Systems</li><li>SIP Trunks</li></ul>
    <a class="btn" href="#">Read More</a>
  </div>
</section>

<section class="abs why">
  <h2 class="section-title">Why Corvane IT</h2>
  <div class="abs why-mark"></div>
  <p class="abs why-text">Lorem ipsum dolor sit amet, consectetur adipiscing elit. Vivamus aliquam non ex et convallis. Curabitur vel rhoncus massa. Aliquam neque nisi, dictum at velit eget, pharetra ornare metus. Curabitur non elementum orci. Integer.</p>
  <a class="btn" href="#">Read More</a>

  <div class="feature" style="left:520px;top:159px">
    <div class="fc"><svg width="34" height="34" viewBox="0 0 34 34" fill="none" stroke="#fff" stroke-width="3"><path d="M5 22v-5a12 12 0 0 1 24 0v5"/><rect x="4" y="19" width="6" height="9" rx="2" fill="#fff"/><rect x="24" y="19" width="6" height="9" rx="2" fill="#fff"/></svg></div>
    <div><h4>Get Support</h4><p>Lorem ipsum dolor sit amet, consectetur adipiscing .</p></div>
  </div>
  <div class="feature" style="left:813px;top:159px">
    <div class="fc"><svg width="32" height="32" viewBox="0 0 32 32"><g fill="#fff"><circle cx="16" cy="16" r="9"/><g stroke="#fff" stroke-width="5"><path d="M16 3v26M3 16h26M7 7l18 18M25 7L7 25"/></g></g><circle cx="16" cy="16" r="4" fill="#58595b"/></svg></div>
    <div><h4>Customer Service</h4><p>Lorem ipsum dolor sit amet, consectetur adipiscing .</p></div>
  </div>
  <div class="feature" style="left:520px;top:312px">
    <div class="fc"><svg width="36" height="30" viewBox="0 0 36 30" fill="#fff"><circle cx="18" cy="8" r="6"/><path d="M8 28a10 10 0 0 1 20 0z"/><circle cx="7" cy="11" r="4"/><circle cx="29" cy="11" r="4"/><path d="M0 25a7 7 0 0 1 9-7 12 12 0 0 0-3 7zM36 25a7 7 0 0 0-9-7 12 12 0 0 1 3 7z"/></svg></div>
    <div><h4>Team Work</h4><p>Lorem ipsum dolor sit amet, consectetur adipiscing .</p></div>
  </div>
  <div class="feature" style="left:813px;top:312px">
    <div class="fc"><svg width="32" height="32" viewBox="0 0 32 32"><circle cx="16" cy="16" r="14" fill="none" stroke="#fff" stroke-width="3"/><rect x="14.5" y="14" width="3" height="10" fill="#fff"/><circle cx="16" cy="9" r="2" fill="#fff"/></svg></div>
    <div><h4>About Us</h4><p>Lorem ipsum dolor sit amet, consectetur adipiscing .</p></div>
  </div>
</section>

<section class="abs testimonials">
  <h2 class="section-title">Testimonials</h2>
  <span class="quote-mark" style="left:340px;top:128px">&ldquo;</span>
  <p class="abs quote">Lorem ipsum dolor sit amet, consectetur adipiscing elit. Vivamus aliquam non ex et convallis. Curabitur vel rhoncus massa. Aliquam neque nisi, dictum at velit eget, pharetra ornare metus. Curabitur non elementum orci. Integer. Quisque vel malesuada neque, non porttitor ipsum. Sed in pharetra massa, a molestie leo</p>
  <span class="quote-mark" style="left:774px;top:228px">&rdquo;</span>
  <div class="arrow" style="left:203px"><svg width="12" height="12" viewBox="0 0 12 12"><path d="M8 1L3 6l5 5" fill="none" stroke="#fff" stroke-width="2"/></svg></div>
  <div class="arrow" style="left:948px"><svg width="12" height="12" viewBox="0 0 12 12"><path d="M4 1l5 5-5 5" fill="none" stroke="#fff" stroke-width="2"/></svg></div>
  <p class="abs author">Dorian Castell</p>
</section>

<footer class="abs footer">
  <div class="brand footer-brand"><span class="dot"></span>Corvane IT</div>
  <div class="abs footer-divider"></div>
  <div class="branch" style="left:424px"><span>Main Number</span><strong>555-010-4400</strong></div>
  <div class="branch" style="left:564px"><span>Houston</span><strong>555-010-4410</strong></div>
  <div class="branch" style="left:704px"><span>San Antonio</span><strong>555-010-4420</strong></div>
  <div class="branch" style="left:842px"><span>Austin</span><strong>555-010-4430</strong></div>
  <div class="branch" style="left:963px"><span>Tulsa</span><strong>555-010-4440</strong></div>
  <div class="abs footer-rule"></div>
  <nav class="abs footer-links"><a href="#">Home</a><b>|</b><a href="#">Services</a><b>|</b><a href="#">Why Corvane IT</a><b>|</b><a href="#">Contact</a></nav>
  <p class="abs copyright">Copyrights @ 2017 All Rights Reserved</p>
</footer>

</body>
</html>
```